Tellmora Corporate Stationery

Look for design of all new corporate stationery for an existing insurance broking business that is going through a redesign and move from older partners to younger family members. New Logo is attached. Company is Brisbane based.
Colours in the Logo is Hex #43bed8 and website features a lot of hex #17b8d8. Website front page "A plan to protect you" - headline. "Professional and Individual advice to protect your greatest assets" - tagline.

Stationery required: Business Cards, Letter head, Thank-you cards, Birthday cards, Presentation folders, With Compliment slips and a powerpoint template. We also would like to send a card to all customers with the something along of the lines of "something new".

Target Market(s)

Customers of Insurance business looking at superannuation, life and income protection insurance, investment advice and wills

Industry/Entity Type

Insurance Broker

Font styles to use
Other font styles liked:
• same as logo

Requirements
Must have
• The above designs for new stationery for the new business including:
• Business Cards, Letter head, Thank-you cards, Birthday cards, Presentation folders, With Compliment slips and a powerpoint template. We also would like to send a card to all customers with the something along of the lines of "something new".
Nice to have
• It is a new look - long time family business being passed to next generation - big focus on advice for YOU, individual advice etc..

```html
<!DOCTYPE html>
<html lang="en">
<head>
<meta charset="utf-8">
<title>Tellmora Business Card</title>
<link rel="stylesheet" href="https://fonts.googleapis.com/css2?family=Open+Sans:ital,wght@0,400;0,600;1,400&display=swap">
<style>
  :root {
    --backdrop: #262626;
    --card-white: #ffffff;
    --brand-blue: #3fbfd9;
    --brand-grey: #808285;
    --text-grey: #5a5a5a;
    --faint-grey: #f0f0f0;
  }
  html, body {
    margin: 0;
    width: 1200px;
    height: 987px;
    overflow: hidden;
    background: var(--backdrop);
    font-family: "Open Sans", Arial, sans-serif;
  }
  .card {
    position: absolute;
    width: 615px;
    height: 352px;
    overflow: hidden;
  }
  .card-front { left: 293px; top: 130px; background: var(--card-white); }
  .card-back { left: 292px; top: 505px; background: var(--brand-blue); }

  .side-strip {
    position: absolute;
    left: 36px; top: 0;
    width: 72px; height: 352px;
    background: var(--brand-blue);
  }
  .side-strip-top {
    position: absolute;
    left: 0; top: 0;
    width: 72px; height: 104px;
    background: var(--brand-grey);
  }
  .brand-dot {
    position: absolute;
    left: 8px; top: 36px;
    width: 56px; height: 56px;
    border-radius: 50%;
    background: var(--card-white);
  }
  .strip-icon {
    position: absolute;
    left: 26px;
    width: 20px; height: 20px;
  }
  .faint-circle {
    position: absolute;
    left: 360px; top: 20px;
    width: 330px; height: 330px;
    border-radius: 50%;
    background: var(--faint-grey);
    opacity: 0.6;
  }
  .brand-name {
    position: absolute;
    left: 124px; top: 46px;
    margin: 0;
    font-size: 30px;
    font-weight: 600;
    letter-spacing: 1px;
    color: var(--brand-blue);
    text-transform: uppercase;
  }
  .person-name {
    position: absolute;
    left: 136px; top: 112px;
    margin: 0;
    font-size: 21px;
    font-weight: 600;
    color: var(--brand-blue);
    text-transform: uppercase;
  }
  .person-role {
    position: absolute;
    left: 136px; top: 138px;
    margin: 0;
    font-size: 16px;
    color: var(--brand-grey);
    text-transform: uppercase;
  }
  .contact-list {
    position: absolute;
    left: 136px; top: 174px;
    margin: 0; padding: 0;
    list-style: none;
    font-size: 16px;
    line-height: 23.4px;
    color: var(--text-grey);
  }
  .contact-address {
    position: absolute;
    left: 136px; top: 303px;
    margin: 0;
    font-size: 16px;
    color: var(--text-grey);
  }

  .back-mark {
    position: absolute;
    left: 420px; top: 232px;
    display: flex;
    align-items: center;
    gap: 10px;
  }
  .back-dot {
    width: 28px; height: 28px;
    border-radius: 50%;
    background: var(--brand-grey);
  }
  .back-name {
    margin: 0;
    font-size: 26px;
    font-weight: 600;
    letter-spacing: 1px;
    color: var(--card-white);
    text-transform: uppercase;
  }
  .back-web {
    position: absolute;
    right: 30px; top: 312px;
    margin: 0;
    font-size: 15px;
    font-style: italic;
    color: var(--card-white);
  }
</style>
</head>
<body>
  <section class="card card-front">
    <div class="faint-circle"></div>
    <div class="side-strip">
      <div class="side-strip-top"></div>
      <div class="brand-dot"></div>
      <svg class="strip-icon" style="top:121px" viewBox="0 0 20 20" aria-hidden="true">
        <circle cx="10" cy="6" r="4.5" fill="#fff"/>
        <path d="M1 20 C1 13 5 11 10 11 C15 11 19 13 19 20 Z" fill="#fff"/>
      </svg>
      <svg class="strip-icon" style="top:175px" viewBox="0 0 20 20" aria-hidden="true">
        <path d="M4 2 L7 2 L8.5 6 L6.5 7.5 C7.5 10 10 12.5 12.5 13.5 L14 11.5 L18 13 L18 16 C18 17 17 18 16 18 C8.5 17.5 2.5 11.5 2 4 C2 3 3 2 4 2 Z" fill="#fff"/>
      </svg>
      <svg class="strip-icon" style="top:198px" viewBox="0 0 20 20" aria-hidden="true">
        <rect x="5" y="1" width="10" height="18" rx="1.5" fill="none" stroke="#fff" stroke-width="2"/>
        <circle cx="10" cy="16" r="1" fill="#fff"/>
      </svg>
      <svg class="strip-icon" style="top:222px" viewBox="0 0 20 20" aria-hidden="true">
        <rect x="5" y="2" width="10" height="5" fill="#fff"/>
        <rect x="1" y="8" width="18" height="7" rx="1" fill="#fff"/>
        <rect x="5" y="13" width="10" height="5" fill="#fff" stroke="#3fbfd9" stroke-width="1"/>
      </svg>
      <svg class="strip-icon" style="top:245px" viewBox="0 0 20 20" aria-hidden="true">
        <rect x="2" y="5" width="16" height="11" fill="#fff"/>
        <path d="M2 5 L10 11 L18 5" fill="none" stroke="#3fbfd9" stroke-width="1.3"/>
      </svg>
      <svg class="strip-icon" style="top:269px" viewBox="0 0 20 20" aria-hidden="true">
        <circle cx="10" cy="10" r="7.5" fill="#fff"/>
        <path d="M6 6 C8 7 8 9 7 11 M12 4 C11 7 13 8 15 8 M11 15 C11 13 13 12 14 13" fill="none" stroke="#3fbfd9" stroke-width="1.3"/>
      </svg>
      <svg class="strip-icon" style="top:303px" viewBox="0 0 20 20" aria-hidden="true">
        <path d="M10 1 C6 1 3.5 4 3.5 7.5 C3.5 12 10 19 10 19 C10 19 16.5 12 16.5 7.5 C16.5 4 14 1 10 1 Z" fill="#fff"/>
        <circle cx="10" cy="7.5" r="2.5" fill="#3fbfd9"/>
      </svg>
    </div>

    <h1 class="brand-name">Tellmora</h1>
    <h2 class="person-name">Mara Quinlan</h2>
    <p class="person-role">CEO/Founder</p>
    <ul class="contact-list">
      <li>07 3184 2260</li>
      <li>0412 775 309</li>
      <li>07 3184 2261</li>
      <li>hello@tellmora.au</li>
      <li>www.tellmora.au</li>
    </ul>
    <p class="contact-address">48 Wattle Street, Brisbane, Queensland 4000</p>
  </section>

  <section class="card card-back">
    <div class="back-mark">
      <div class="back-dot"></div>
      <p class="back-name">Tellmora</p>
    </div>
    <p class="back-web">www.tellmora.au</p>
  </section>
</body>
</html>
```